Mortgage Company ready to make a statement!

We have a basic logo that I am fairly happy with ... but it could use a little bit of tweaking before we order the sign for our building. We also want some knock-your-socks-off business cards.
Problem: Inside of our Mortgage Office (Bright Fern Mortgage Group), we are going to have a coffee lounge (Sunbrew Cafe) for Realtors to use instead of the local Cuppington to meet with homebuyers. The office and coffee lounge are in an industrial building and is decorated with cozy overstuffed chairs, a hodge podge of interesting lamps and furniture, and goal is to make it as inviting as possible. However, we are a financial institution... so we need to keep it pretty clean as well.
One of my favorite marketing ideas is to cut a house key for everyone who buys a home using us with a key that matches our logo. There's only one key shape that works really well, so that needs to match the logo in order for the idea to work. I'll attach an image of the key blank.... although the way the key hole cut out looks terrible, so I was thinking of having them just do a thin outline instead.
Would like a similar, matching logo for the Sunbrew Cafe... but possibly something that would be a little less formal and would be cute on a coffee mug- nothing stuffy.
AND, we're opening a home inspection company as well, and we would like that logo and branding to match. The home inspection company is "Bright Fern Home Inspections"
We were thinking that for the home inspection company , we could use a magnifying glass shape inside of the house shape for the logo, use a keyhole shape inside of the same house for the mortgage company, and use a coffee cup inside of the house shape for Sunbrew Cafe.
Just getting stuck and need to help. I designed the attached logo myself, and that is what we are currently using. Designers at local printing companies have failed to impress us.
The mortgage industry has a lot of numbers and logos, etc that they require us to put on our business cards... so it's hard to keep them looking clean.
HELP! HELP! :)

```html
<!DOCTYPE html>
<html lang="en">
<head>
<meta charset="utf-8">
<title>Bright Fern Mortgage Group – Business Card</title>
<link rel="stylesheet" href="https://fonts.googleapis.com/css2?family=Marcellus&family=Montserrat:wght@400;500;600&display=swap">
<style>
  :root {
    --brand-blue: #246385;
    --ink: #3d3f44;
    --ink-soft: #5a5c60;
    --band-grey: #58595b;
    --paper: #ffffff;
    --backdrop: #eeede9;
  }
  * { margin: 0; padding: 0; box-sizing: border-box; }
  html, body { width: 1200px; height: 929px; overflow: hidden; background: var(--backdrop); }
  .stage { position: relative; width: 1200px; height: 929px; }

  .card { position: absolute; width: 580px; height: 330px; overflow: hidden;
          box-shadow: 0 6px 14px rgba(0,0,0,.18); }

  /* Front */
  .card--front { left: 70px; top: 80px; background: var(--brand-blue); }
  .front__map { position: absolute; left: 70px; top: 40px; width: 440px; height: 250px;
                border-radius: 50%;
                background: radial-gradient(ellipse at center, rgba(20,70,100,.45), rgba(20,70,100,0) 70%); }
  .wordmark { position: absolute; display: flex; align-items: center; gap: 12px;
              font-family: "Marcellus", serif; font-weight: 400; white-space: nowrap; }
  .wordmark__dot { width: 14px; height: 14px; border-radius: 50%; }
  .card--front .wordmark { left: 0; right: 0; top: 145px; justify-content: center;
                           color: var(--paper); font-size: 30px; letter-spacing: .5px; }
  .card--front .wordmark__dot { background: var(--paper); }

  /* Back */
  .card--back { left: 560px; top: 480px; background: var(--paper); }
  .card--back .wordmark { left: 44px; top: 96px; color: var(--brand-blue); font-size: 23px; }
  .card--back .wordmark__dot { background: var(--brand-blue); width: 12px; height: 12px; }

  .back__tab { position: absolute; right: 0; top: 60px; width: 8px; height: 44px;
               background: var(--brand-blue); border-radius: 6px 0 0 6px; }

  .person__name { position: absolute; right: 40px; top: 148px; text-align: right;
                  font-family: "Marcellus", serif; font-size: 23px; color: var(--brand-blue);
                  letter-spacing: 1px; line-height: 28px; }
  .person__rule { position: absolute; right: 96px; top: 182px; width: 330px; height: 1.5px;
                  background: var(--brand-blue); }
  .person__role { position: absolute; right: 40px; top: 180px; font-family: "Montserrat", sans-serif;
                  font-weight: 600; font-size: 13px; line-height: 16px; color: var(--ink-soft); }
  .address { position: absolute; right: 40px; top: 208px; text-align: right;
             font-family: "Montserrat", sans-serif; font-size: 11.5px; line-height: 15px;
             color: var(--ink); letter-spacing: .5px; }

  .contacts__rule { position: absolute; left: 34px; top: 224px; width: 240px; height: 1.5px;
                    background: var(--brand-blue); }
  .contacts { position: absolute; left: 40px; top: 234px; list-style: none;
              font-family: "Montserrat", sans-serif; font-size: 12.5px; color: var(--ink); }
  .contacts li { display: flex; align-items: center; gap: 10px; height: 18px; letter-spacing: .4px; }
  .contacts svg { width: 11px; height: 11px; fill: var(--brand-blue); flex: none; }

  .band { position: absolute; bottom: 0; }
  .band--blue { left: 0; width: 452px; height: 22px; background: var(--brand-blue); }
  .band--grey { left: 458px; right: 0; height: 36px; background: var(--band-grey); }
</style>
</head>
<body>
<main class="stage">
  <section class="card card--front" aria-label="Card front">
    <div class="front__map" role="img" aria-label="Faint world map in darker blue"></div>
    <div class="wordmark"><span class="wordmark__dot"></span>Bright Fern Mortgage Group</div>
  </section>

  <section class="card card--back" aria-label="Card back">
    <div class="back__tab"></div>
    <div class="wordmark"><span class="wordmark__dot"></span>Bright Fern Mortgage Group</div>

    <p class="person__name">DANA WHITLOCK</p>
    <div class="person__rule"></div>
    <p class="person__role">CEO</p>
    <p class="address">Harbour Point Centre<br>Riverton Eastgate</p>

    <div class="contacts__rule"></div>
    <ul class="contacts">
      <li><svg viewBox="0 0 12 12"><rect x="3" y="0.5" width="6" height="11" rx="1" fill="none" stroke="#246385" stroke-width="1.2"/></svg>000-123-4567</li>
      <li><svg viewBox="0 0 12 12"><rect x="3" y="0.5" width="6" height="3"/><rect x="0.5" y="4" width="11" height="5" rx="1"/><rect x="3" y="8" width="6" height="3.5"/></svg>000-123-4567</li>
      <li><svg viewBox="0 0 12 12"><rect x="0.5" y="2" width="11" height="8"/><path d="M0.5 2 L6 6.5 L11.5 2" fill="none" stroke="#fff" stroke-width="1"/></svg>dana.whitlock@brightfernmg.com</li>
    </ul>

    <div class="band band--blue"></div>
    <div class="band band--grey"></div>
  </section>
</main>
</body>
</html>
```